Direct Mail Condition Reporting Flyer

This is a quality control service that is designed to
detect direct mail such as letters, magazines and catalogs that are delivered by the Vellmark Courier Bureau in poor condition. Attached are actual samples of mail delivered in poor condition and our company logo. We generally use the Red and Blue colors of the Vellmark Courier Bureau.

Target Market(s)

Direct mailers from every Industry

Industry/Entity Type

It Service

Font styles to use
Sans Serif

Colors
ec1f27
0555a3

Requirements
Must have
• It needs to look professional. It will be placed on a table at a trade conference and inserted into a folder with other material.

```html
<!DOCTYPE html>
<html lang="en">
<head>
<meta charset="utf-8">
<title>Mail Condition Reporting Flyer</title>
<link rel="stylesheet" href="https://fonts.googleapis.com/css2?family=Oswald:wght@300;400;500;600&family=Roboto+Condensed:wght@300;400;700&display=swap">
<style>
  :root {
    --page-bg: #d9d9d9;
    --navy: #1f3f99;
    --navy-deep: #1b3a8f;
    --blue-glow: #3f7fd8;
    --brand-blue: #1d3f94;
    --brand-red: #d31f2e;
    --white: #ffffff;
    --grey-text: #555a60;
  }
  * { margin: 0; padding: 0; box-sizing: border-box; }
  html, body { width: 1200px; height: 1000px; overflow: hidden; background: var(--page-bg); }
  .flyer {
    position: absolute; left: 212px; top: 0; width: 776px; height: 1000px;
    background: var(--white); overflow: hidden;
    font-family: "Roboto Condensed", "Arial Narrow", sans-serif; color: var(--white);
  }
  .masthead {
    position: absolute; left: 0; top: 0; width: 100%; height: 178px;
    background: var(--navy-deep); text-align: center;
  }
  .masthead__lead {
    position: absolute; left: 0; right: 0; top: 40px;
    font-family: "Oswald", sans-serif; font-weight: 300; font-size: 43px; line-height: 1; letter-spacing: -0.5px;
  }
  .masthead__title {
    position: absolute; left: 0; right: 0; top: 90px;
    font-family: "Oswald", sans-serif; font-weight: 600; font-size: 62px; line-height: 1; letter-spacing: -1px;
  }
  .samples {
    position: absolute; left: 0; top: 178px; width: 100%; height: 304px;
    background: linear-gradient(100deg, #c9c2b6 0%, #a89c8e 30%, #d5d0c8 55%, #8f8378 75%, #b9b1a6 100%);
  }
  .pitch {
    position: absolute; left: 0; top: 482px; width: 100%; height: 334px;
    background: radial-gradient(ellipse 70% 55% at 50% 0%, var(--blue-glow) 0%, #2a59b8 45%, var(--navy) 100%);
    text-align: center;
  }
  .pitch__question {
    position: absolute; left: 0; right: 0; top: 40px;
    font-family: "Oswald", sans-serif; font-weight: 500; font-size: 26.5px; line-height: 1; letter-spacing: -0.2px;
  }
  .pitch__sub {
    position: absolute; left: 0; right: 0; top: 80px;
    font-family: "Oswald", sans-serif; font-weight: 300; font-size: 22.5px; line-height: 32px; letter-spacing: -0.3px;
  }
  .pitch__intro {
    position: absolute; left: 66px; right: 66px; top: 184px;
    font-family: "Oswald", sans-serif; font-weight: 400; font-size: 15.5px; line-height: 21px;
  }
  .point { position: absolute; top: 245px; height: 54px; text-align: left; }
  .point__num {
    position: absolute; left: 0; top: -12px;
    font-family: "Oswald", sans-serif; font-weight: 600; font-size: 64px; line-height: 70px; letter-spacing: -2px;
  }
  .point__text {
    position: absolute; top: 0;
    font-family: "Oswald", sans-serif; font-weight: 300; font-size: 13.5px; line-height: 19.5px;
  }
  .point--one { left: 43px; } .point--one .point__text { left: 39px; width: 214px; }
  .point--two { left: 344px; } .point--two .point__text { left: 47px; width: 162px; }
  .point--three { left: 605px; } .point--three .point__text { left: 40px; width: 96px; }
  .footer { position: absolute; left: 0; top: 816px; width: 100%; height: 184px; background: var(--white); }
  .brand__name {
    position: absolute; left: 46px; top: 88px;
    display: flex; align-items: center; gap: 10px;
    font-family: "Roboto Condensed", sans-serif; font-weight: 700; font-size: 25px; line-height: 30px; letter-spacing: 4px; color: var(--brand-blue);
  }
  .brand__square { width: 14px; height: 14px; background: var(--brand-red); }
  .brand__tagline {
    position: absolute; left: 192px; top: 123px; white-space: nowrap;
    font-family: "Roboto Condensed", sans-serif; font-weight: 700; font-size: 13px; color: var(--grey-text);
  }
  .contact { position: absolute; right: 44px; top: 12px; text-align: right; }
  .contact__note {
    font-family: "Oswald", sans-serif; font-weight: 300; font-size: 13px; line-height: 16px; color: var(--grey-text); width: 236px; margin-left: auto;
  }
  .contact__web { margin-top: 8px; font-family: "Oswald", sans-serif; font-size: 31px; line-height: 1; color: var(--brand-blue); font-weight: 300; letter-spacing: -0.5px; }
  .contact__web strong { color: var(--brand-red); font-weight: 600; }
  .contact__web b { font-weight: 500; }
  .contact__phone { margin-top: 2px; font-family: "Oswald", sans-serif; font-size: 30px; line-height: 1; color: var(--brand-blue); }
  .contact__phone em { font-weight: 300; font-style: italic; }
  .contact__phone strong { font-weight: 600; }
</style>
</head>
<body>
<main class="flyer">
  <header class="masthead">
    <p class="masthead__lead">How much of your mail is</p>
    <h1 class="masthead__title">BEING DELIVERED LIKE THIS?</h1>
  </header>

  <div class="samples" role="img" aria-label="Photographs of torn, creased and damaged envelopes, seminar mailers and catalogs delivered in poor condition"></div>

  <section class="pitch">
    <h2 class="pitch__question">Is poor condition affecting the delivery of your mail?</h2>
    <p class="pitch__sub">Will your company’s reputation suffer when customers receive damaged mailings?<br>Are missing inserts hurting your response rate?</p>
    <p class="pitch__intro">ClearTrace has developed a comprehensive mail condition reporting service that answers these questions in<br>response to the increased incidence of mailings being delivered in poor condition.&nbsp; You learn:</p>

    <div class="point point--one">
      <span class="point__num">1.</span>
      <p class="point__text">If your direct mail or catalogs are received torn, creased, smudged, wrinkled, stained or with water damage.</p>
    </div>
    <div class="point point--two">
      <span class="point__num">2.</span>
      <p class="point__text">Whether there are printing errors or problems with ink jetting and addressing.</p>
    </div>
    <div class="point point--three">
      <span class="point__num">3.</span>
      <p class="point__text">If contents are missing after mail is opened.</p>
    </div>
  </section>

  <footer class="footer">
    <div class="brand__name"><span class="brand__square"></span>CLEARTRACE</div>
    <p class="brand__tagline">Clear Reports for Every Mailing.</p>
    <div class="contact">
      <p class="contact__note">You have the ability to receive scanned images or to have the damaged pieces returned. Custom programs are available. Request a quote at</p>
      <p class="contact__web"><strong>cleartrace</strong><b>.com</b>/condition</p>
      <p class="contact__phone"><em>or call</em> <strong>(555) 014-2276</strong></p>
    </div>
  </footer>
</main>
</body>
</html>
```